Real Estate Brokerage Stationery Designs

I am looking to have presentation folders with business card slots on both sides along with pockets on both sides. I've attached logos, website colors along with current business card designs.

I am looking for envelope designs both big and small. Possibly new business card designs, notepad templates for big and small notepads. Letterhead designs. Pop socket designs. Realtors name badge designs.

www.brightholdrealty.example

```html
<!DOCTYPE html>
<html lang="en">
<head>
<meta charset="utf-8">
<title>Brighthold Realty Stationery</title>
<link href="https://fonts.googleapis.com/css2?family=Roboto:wght@400;500;700&family=Questrial&display=swap" rel="stylesheet">
<style>
:root{
  --brand-blue:#0a52ad;
  --ink:#1d1d1d;
  --body-grey:#6a6a6a;
  --rule-grey:#b5b5b6;
  --paper:#f0f0f0;
  --paper-white:#ffffff;
  --envelope:#f6f6f6;
  --backdrop:#dedede;
}
*{margin:0;padding:0;box-sizing:border-box}
html,body{width:1200px;height:1200px;overflow:hidden}
body{background:var(--backdrop);font-family:'Roboto',sans-serif;color:var(--ink);position:relative}
.sheet{position:absolute}
.wordmark{font-family:'Roboto',sans-serif;font-weight:700;color:var(--brand-blue);display:flex;align-items:center;gap:6px;line-height:1.05}
.wordmark .mark-square{background:var(--brand-blue);flex:none}

/* Letterhead */
.letterhead{left:51px;top:216px;width:555px;height:784px;background:var(--paper)}
.letterhead .edge-bar{position:absolute;left:0;top:35px;width:13px;height:112px;background:var(--brand-blue)}
.letterhead .edge-bar.right{left:auto;right:0;background:var(--rule-grey)}
.letterhead .wordmark{position:absolute;left:51px;top:70px;font-size:24px;width:140px}
.letterhead .wordmark .mark-square{width:18px;height:18px}
.contact{position:absolute;left:377px;top:50px;font-size:7.8px;line-height:11.3px}
.contact .address{color:var(--brand-blue);font-weight:700;margin-bottom:7px;font-size:7.8px;line-height:10.5px}
.contact-row{display:flex;align-items:center;gap:5px}
.contact-row svg{width:7px;height:7px;flex:none}
.contact .link{color:var(--brand-blue)}
.letter-body{position:absolute;left:50px;top:220px;width:451px;font-family:'Questrial',sans-serif;color:var(--body-grey)}
.letter-body .salutation{font-size:14px;color:#555;margin-bottom:21px}
.letter-body p{font-size:8.6px;line-height:12px;text-align:justify;margin-bottom:12px}
.letter-body .closing{margin-top:24px;font-size:8.6px}
.signature{position:absolute;left:42px;top:548px;width:100px;height:40px;background:linear-gradient(90deg,rgba(10,82,173,.18),rgba(10,82,173,.08));border-radius:4px}
.letterhead .foot-rule{position:absolute;left:94px;top:769px;width:367px;height:5px;background:var(--brand-blue)}

/* Business card front */
.card-front{left:616px;top:216px;width:268px;height:162px;background:var(--paper-white);overflow:hidden}
.card-front .wordmark{position:absolute;left:22px;top:30px;font-size:13px;width:80px}
.card-front .wordmark .mark-square{width:10px;height:10px}
.card-front .name-band{position:absolute;left:0;top:65px;width:268px;height:23px;background:var(--brand-blue);color:#fff;padding:3px 0 0 21px}
.name-band .agent{font-size:10.5px;font-weight:700;letter-spacing:.2px;line-height:11px}
.name-band .role{font-size:5.5px;line-height:7px}
.badge{position:absolute;background:#fff;border-radius:1px}
.agent-photo{position:absolute;left:145px;top:9px;width:123px;height:153px;background:linear-gradient(180deg,#e8e8e8 0%,#8a8f96 45%,#2a2d33 100%)}
.card-front .card-contact{position:absolute;left:21px;top:94px;font-size:6px;line-height:8px}
.card-contact .addr{margin-bottom:3px}
.card-contact .contact-row{gap:4px}
.card-contact .contact-row svg{width:5px;height:5px}

/* Business card back */
.card-back{left:900px;top:216px;width:269px;height:162px;background:var(--paper-white)}
.card-back .wordmark{position:absolute;left:0;right:0;top:62px;justify-content:center;font-size:17px}
.card-back .wordmark .mark-square{width:12px;height:12px}
.card-back .services{position:absolute;left:0;right:0;top:125px;text-align:center;font-size:6.6px;line-height:9.5px}
.sep{color:var(--brand-blue);margin:0 3px}

/* Envelope back */
.envelope-back{left:615px;top:433px;width:554px;height:252px;background:var(--envelope)}
.envelope-back svg.flap{position:absolute;left:0;top:0}
.envelope-back .services{position:absolute;left:0;right:0;top:211px;text-align:center;font-size:10px;line-height:14px;color:var(--brand-blue)}
.envelope-back .sep{margin:0 4px}

/* Envelope front */
.envelope-front{left:615px;top:739px;width:556px;height:253px;background:var(--envelope)}
.envelope-front .wordmark{position:absolute;left:33px;top:80px;font-size:16px;width:110px}
.envelope-front .wordmark .mark-square{width:12px;height:12px}
.envelope-front .return-address{position:absolute;left:29px;top:115px;width:100px;text-align:center;font-size:6px;line-height:8px}
.envelope-front .foot-rule{position:absolute;left:94px;top:240px;width:368px;height:5px;background:var(--brand-blue)}
</style>
</head>
<body>

<section class="sheet letterhead">
  <div class="edge-bar"></div>
  <div class="edge-bar right"></div>
  <div class="wordmark"><span class="mark-square"></span><span>Brighthold Realty</span></div>

  <div class="contact">
    <div class="address">2400 Harbor Lane,<br>Suite 310, Cedar Point FL 3341</div>
    <div class="contact-row"><svg viewBox="0 0 8 8"><rect x="2" y="0.5" width="4" height="7" rx="0.8" fill="none" stroke="#0a52ad" stroke-width="1"/></svg>555-201-4478</div>
    <div class="contact-row"><svg viewBox="0 0 8 8"><path d="M1 1.5 L2.8 1 L3.6 3 L2.6 3.6 Q3.4 5 4.5 5.5 L5.1 4.5 L7 5.2 L6.5 7 Q2 6.5 1 1.5Z" fill="#0a52ad"/></svg>555-318-2264</div>
    <div class="contact-row"><svg viewBox="0 0 8 8"><rect x="2" y="0.5" width="4" height="2" fill="#0a52ad"/><rect x="0.5" y="3" width="7" height="3" rx="0.6" fill="#0a52ad"/><rect x="2" y="5.5" width="4" height="2" fill="#0a52ad"/></svg>555-427-9051</div>
    <div class="contact-row"><svg viewBox="0 0 8 8"><rect x="0.5" y="1.5" width="7" height="5" rx="0.6" fill="#0a52ad"/><path d="M0.8 2 L4 4.5 L7.2 2" fill="none" stroke="#fff" stroke-width="0.8"/></svg>marcus@brightholdrealty.example</div>
    <div class="contact-row"><svg viewBox="0 0 8 8"><circle cx="4" cy="4" r="3.4" fill="#0a52ad"/><path d="M0.6 4 H7.4 M4 0.6 Q2 4 4 7.4 M4 0.6 Q6 4 4 7.4" stroke="#fff" stroke-width="0.5" fill="none"/></svg>www.<span class="link">brightholdrealty</span>.example</div>
  </div>

  <div class="letter-body">
    <div class="salutation">Dear Mr. Smith,</div>
    <p>Lorem ipsum dolor sit amet, consectetur adipiscing elit. Donec orci purus, luctus vitae dignissim eu, iaculis sed purus. Vivamus faucibus, ipsum nec aliquet viverra, leo mauris condimentum ligula, sit amet sagittis enim ligula quis arcu. Nam egestas tortor id nisi porttitor mattis. In tortor ante, ultricies in suscipit a, tempus non massa. Vivamus et auctor mi. Fusce vel massa nulla. Phasellus nec eros mauris, et scelerisque orci.</p>
    <p>Donec malesuada orci vitae nulla accumsan porta a id massa. Quisque accumsan iaculis magna sit amet fringilla. Maecenas consequat, magna eget tincidunt semper, odio nibh rutrum mi, id feugiat ante nisi eu risus. Vestibulum nunc orci, rhoncus a placerat in, ultricies in mi. Cras mattis varius eros, vel fringilla nisi suscipit eget. Quisque scelerisque sagittis nulla at porttitor.</p>
    <p>Sed id augue vitae urna euismod commodo aliquet a quam. Pellentesque arcu velit, cursus et malesuada ut, consequat et diam. Nullam erat sem, rhoncus id ullamcorper vitae, rhoncus et arcu. In ultricies ultricies nulla, ut rutrum nisi iaculis at. Donec eu magna a metus ornare faucibus. Fusce aliquet faucibus ultricies. Morbi semper, est id tincidunt gravida, sem arcu adipiscing lacus, ac bibendum nulla leo eu purus. Quisque nec diam sed risus consectetur a ccumsan quis quis nibh. Vestibulum id purus lorem.</p>
    <p>It is a long established fact that a reader will be distracted by the readable content of a page when looking at its layout. The point of using Lorem Ipsum is that it has a more-or-less normal distribution of letters, as opposed to using 'Content here, content here', making it look like readable English. Many desktop publishing packages</p>
    <div class="closing">Sincerely,</div>
  </div>
  <div class="signature" role="img" aria-label="Handwritten signature"></div>
  <div class="foot-rule"></div>
</section>

<section class="sheet card-front">
  <div class="wordmark"><span class="mark-square"></span><span>Brighthold Realty</span></div>
  <div class="name-band">
    <div class="agent">MARCUS ELLERY</div>
    <div class="role">REALTOR®</div>
  </div>
  <div class="badge" style="left:120px;top:71px;width:10px;height:10px"></div>
  <div class="badge" style="left:138px;top:71px;width:8px;height:10px"></div>
  <div class="badge" style="left:148px;top:74px;width:14px;height:7px"></div>
  <div class="agent-photo" role="img" aria-label="Portrait photo of the agent in a dark suit"></div>
  <div class="card-contact">
    <div class="addr">2400 Harbor Lane,<br>Suite 310, Cedar Point FL 3341</div>
    <div class="contact-row"><svg viewBox="0 0 8 8"><rect x="2" y="0.5" width="4" height="7" rx="0.8" fill="none" stroke="#0a52ad" stroke-width="1.2"/></svg>555-201-4478</div>
    <div class="contact-row"><svg viewBox="0 0 8 8"><circle cx="4" cy="4" r="3.5" fill="#0a52ad"/></svg>555-318-2264</div>
    <div class="contact-row"><svg viewBox="0 0 8 8"><rect x="0.5" y="2" width="7" height="4.5" rx="0.6" fill="#0a52ad"/></svg>555-427-9051</div>
    <div class="contact-row"><svg viewBox="0 0 8 8"><rect x="0.5" y="1.5" width="7" height="5" rx="0.6" fill="#0a52ad"/></svg>marcus@brightholdrealty.example</div>
    <div class="contact-row"><svg viewBox="0 0 8 8"><circle cx="4" cy="4" r="3.5" fill="#0a52ad"/></svg>www.brightholdrealty.example</div>
  </div>
</section>

<section class="sheet card-back">
  <div class="wordmark"><span class="mark-square"></span><span>Brighthold Realty</span></div>
  <div class="services">
    Residential Real Estate<span class="sep">|</span>Commercial Real Estate<br>
    Property Management<span class="sep">|</span>Investments
  </div>
</section>

<section class="sheet envelope-back">
  <svg class="flap" width="554" height="82" viewBox="0 0 554 82">
    <path d="M0 0 H554 L548 18 Q536 78 500 82 H54 Q18 78 6 18 Z" fill="#0a52ad"/>
  </svg>
  <div class="services">
    Residential Real Estate<span class="sep">|</span>Commercial Real Estate<br>
    Property Management<span class="sep">|</span>Investments
  </div>
</section>

<section class="sheet envelope-front">
  <div class="wordmark"><span class="mark-square"></span><span>Brighthold Realty</span></div>
  <div class="return-address">2400 Harbor Lane,<br>Suite 310, Cedar Point FL 3341</div>
  <div class="foot-rule"></div>
</section>

</body>
</html>
```